Website redesign for Halt and Fullmane

We would like to update the design of our current website to a more concise, conversion optimized design.
The goal of our website is to get our message across as concisely as possible plus encourage people to contact us for more information or to book a consultation.
We need a redesign of the home page and 1 internal page - just for design/layout purposes/format purposes.

Target Market(s)

Males 20-45 years old who are concerned about hair loss and who want to regrow their own hair.

Industry/Entity Type

Health And Wellness

Number of Pages Required

2 page

Font styles to use
Sans Serif

Colors
00a990
33a6d7
ffffff
9d9d9d

Requirements
Must have
• We want the home page to be very concise and to the point in getting the message across. We want to get across the following 6 key messages:
• 1. Dr Pembrook story – why he created this solution
• 2. Hair loss is caused by a chemical imbalance
• 3. Halt and fullmane conducts genetic and DNA analysis, then rebalances body chemistry, thus reversing the hair loss process and enabling your own hair to regrow naturally
• 4. Money back guaranteed results
• 5. Purely Core ingredients – no harsh preservatives or chemicals are included
• 6. All ingredients are FDA approved and safe – no side effects
• We also need a strong call to action. We want people to call or email us to find out more information or to schedule a consultation.
• Here is our current website which is not performing as we would hope: http://www.haltandfullmane.example/
• Here is our press release for further information: https://www.pressdeskhub.example/news/finally-we-now-have-a-cure-for-male-pattern-baldness-28461902
• I uploaded the logo files, but let me know if anything else is needed and I can add it.

```html
<!DOCTYPE html>
<html lang="en">
<head>
<meta charset="utf-8">
<title>Halt &amp; Fullmane – Home</title>
<link href="https://fonts.googleapis.com/css2?family=Open+Sans:wght@400;600;700;800&display=swap" rel="stylesheet">
<style>
:root{
  --green:#00a990;
  --blue:#33a6d7;
  --white:#ffffff;
  --grey:#9d9d9d;
  --ink:#3b3b3b;
  --light:#eeeef0;
  --hero-a:#8f9aa3;
  --hero-b:#d8d2cc;
}
*{box-sizing:border-box;margin:0;padding:0}
html,body{width:1200px;height:3303px;overflow:hidden;background:var(--white)}
body{font-family:"Open Sans",Arial,sans-serif;color:var(--ink);position:relative}
.abs{position:absolute}
.site-header{position:absolute;left:0;top:0;width:1200px;height:115px;background:var(--white)}
.brand{position:absolute;left:132px;top:24px;display:flex;align-items:center;gap:14px;color:#2e6a73;font-weight:400}
.brand-mark{width:44px;height:44px;background:var(--green)}
.brand-name{font-size:30px;line-height:34px}
.brand-by{font-size:19px;line-height:24px;padding-left:60px}
.call{position:absolute;left:632px;top:30px;display:flex;align-items:center;gap:18px}
.call-divider{width:1px;height:48px;background:#ccc}
.call small{display:block;font-size:11px;color:var(--ink)}
.call strong{display:block;font-size:23px;color:var(--green);font-weight:600}
.follow{position:absolute;left:931px;top:30px;font-size:11px}
.social{display:flex;gap:4px;margin-top:14px}
.social span{width:22px;height:22px;border-radius:50%;background:var(--blue)}
.social span:nth-child(3){background:#dd4b39}
.social span:nth-child(4){background:#3b6fb0}
.social span:nth-child(6){background:#e02a20}
.main-nav{position:absolute;left:0;top:115px;width:1200px;height:39px;background:var(--blue)}
.main-nav ul{list-style:none;display:flex;justify-content:space-between;margin:0 132px;height:39px;align-items:center}
.main-nav li{color:var(--white);font-size:11.5px;font-weight:700;text-transform:uppercase}
.hero{position:absolute;left:0;top:154px;width:1200px;height:577px;background:linear-gradient(100deg,var(--hero-a),var(--hero-b) 55%,#b7aea6)}
.hero-title{position:absolute;left:105px;top:198px;width:538px;padding:14px 30px;background:rgba(40,40,40,.45);color:var(--white);font-size:35px;font-weight:700;line-height:47px;text-transform:uppercase}
.dots{position:absolute;left:548px;top:517px;display:flex;gap:12px}
.dots span{width:10px;height:10px;border-radius:50%;background:rgba(255,255,255,.6)}
.dots span:nth-child(2){background:transparent;border:2px solid var(--white)}
.section-title{position:absolute;left:50%;transform:translateX(-50%);height:60px;border:3px solid var(--green);color:var(--green);font-size:24px;font-weight:600;display:flex;align-items:center;justify-content:center;text-transform:uppercase;background:var(--white);white-space:nowrap}
.on-green{background:transparent;border-color:var(--white);color:var(--white)}
.intro{position:absolute;left:330px;top:841px;width:540px;text-align:center;font-size:14.5px;line-height:21px}
.team-photo{position:absolute;left:194px;top:936px;width:841px;height:310px;background:linear-gradient(90deg,#efe7e2,#d9c4b6 30%,#9ab8b0 50%,#d9c4b6 70%,#efe7e2)}
.play{position:absolute;left:563px;top:1069px;width:72px;height:72px;border-radius:50%;background:var(--blue)}
.btn{position:absolute;background:var(--green);color:var(--white);font-size:15px;font-weight:700;text-transform:uppercase;display:flex;align-items:center;justify-content:center}
.key-messages{position:absolute;left:0;top:1246px;width:1200px;height:610px;background:var(--green)}
.key-line{position:absolute;left:599px;top:137px;width:1px;height:433px;background:rgba(255,255,255,.45)}
.key-item{position:absolute;color:var(--white);font-size:14.5px;line-height:21px;width:400px}
.key-item.left{left:58px;text-align:right}
.key-item.right{left:733px}
.key-icon{position:absolute;width:70px;height:70px}
.how-it-works{position:absolute;left:0;top:1856px;width:1200px;height:584px;background:var(--light)}
.step-num{position:absolute;width:70px;height:70px;border-radius:50%;background:var(--blue);color:var(--white);font-size:28px;display:flex;align-items:center;justify-content:center}
.step{position:absolute;width:240px;text-align:center}
.step h3{font-size:14.5px;font-weight:400;line-height:21px;color:var(--ink)}
.step p{margin-top:14px;font-size:11.5px;line-height:18px;color:var(--grey)}
.story-photo{position:absolute;top:2633px;width:131px;height:121px;background:linear-gradient(180deg,#5a4a3e,#8b7568 60%,#8e7bb3)}
.nav-arrow{position:absolute;top:2671px;width:44px;height:44px;border-radius:50%;background:#c2c2c2}
.story-caption{position:absolute;left:0;top:2800px;width:1200px;text-align:center;font-size:17px;color:var(--ink)}
.story-text{position:absolute;left:314px;top:2836px;width:572px;text-align:center;font-size:13px;line-height:22px}
.site-footer{position:absolute;left:0;top:2986px;width:1200px;height:317px;background:var(--blue);color:var(--white)}
.footer-brand{position:absolute;left:132px;top:62px;display:flex;gap:14px;align-items:center;color:var(--white)}
.footer-brand .brand-mark{background:var(--white)}
.site-footer h4{position:absolute;font-size:11.5px;font-weight:700;text-transform:uppercase}
.footer-line{position:absolute;font-size:11.5px;line-height:19px}
.footer-divider{position:absolute;left:132px;top:226px;width:936px;height:1px;background:rgba(255,255,255,.4)}
.copyright{position:absolute;left:0;top:262px;width:1200px;text-align:center;font-size:11px}
</style>
</head>
<body>

<header class="site-header">
  <div class="brand">
    <div class="brand-mark"></div>
    <div><div class="brand-name">Halt &amp; Fullmane</div><div class="brand-by">by Graham Pembrook M.D.</div></div>
  </div>
  <div class="call">
    <svg width="18" height="22" viewBox="0 0 24 24"><path fill="#00a990" d="M6.6 10.8a15 15 0 0 0 6.6 6.6l2.2-2.2a1 1 0 0 1 1-.25 11.4 11.4 0 0 0 3.6.57 1 1 0 0 1 1 1V20a1 1 0 0 1-1 1A17 17 0 0 1 3 4a1 1 0 0 1 1-1h3.5a1 1 0 0 1 1 1c0 1.25.2 2.45.57 3.57a1 1 0 0 1-.25 1z"/></svg>
    <div class="call-divider"></div>
    <div><small>CALL US NOW :</small><strong>(425) 555-0148</strong></div>
  </div>
  <div class="follow">FOLLOW US
    <div class="social"><span></span><span></span><span></span><span></span><span></span><span></span></div>
  </div>
</header>

<nav class="main-nav">
  <ul><li>About us</li><li>How it works</li><li>Success stories</li><li>FAQs</li><li>Blog</li><li>Salon partners</li><li>Book now</li><li>Contact</li></ul>
</nav>

<section class="hero" role="img" aria-label="Portrait of a man with a full head of hair, hand running through it">
  <h1 class="hero-title">The first non-surgical hair loss solution</h1>
  <div class="dots"><span></span><span></span><span></span><span></span><span></span></div>
</section>

<section>
  <h2 class="section-title" style="top:760px;width:320px">Welcome to our site</h2>
  <p class="intro">Dr. Graham Pembrook is a renowned hair restoration expert and was even a contributor in the development of the Advanced High Density MICROscopic single hair transplant procedure.</p>
  <div class="team-photo" role="img" aria-label="Clinic team in white coats standing together"></div>
  <svg class="play" viewBox="0 0 72 72"><circle cx="36" cy="36" r="36" fill="#33a6d7"/><path d="M29 23l20 13-20 13z" fill="#fff"/></svg>
  <div class="btn" style="left:522px;top:1206px;width:154px;height:40px">Read more</div>
</section>

<section class="key-messages">
  <h2 class="section-title on-green" style="top:57px;width:262px">6 key messages</h2>
  <div class="key-line"></div>

  <svg class="key-icon" style="left:482px;top:192px" viewBox="0 0 70 70"><circle cx="35" cy="35" r="34" fill="#fff"/><path d="M22 44h26M27 44c0-8 16-8 16 0M35 22v14M30 26v8M40 26v8" stroke="#00a990" stroke-width="3" fill="none" stroke-linecap="round"/></svg>
  <p class="key-item left" style="top:206px">Dr Pembrook story –<br>why he created this solution</p>
  <svg class="key-icon" style="left:641px;top:192px" viewBox="0 0 70 70"><circle cx="35" cy="35" r="34" fill="#fff"/><path d="M24 40h22v8H24zM35 22v14M29 27l6 9 6-9" stroke="#00a990" stroke-width="3" fill="none" stroke-linejoin="round"/></svg>
  <p class="key-item right" style="top:206px">Hair loss is caused by a<br>chemical imbalance</p>

  <svg class="key-icon" style="left:482px;top:320px" viewBox="0 0 70 70"><circle cx="35" cy="35" r="34" fill="#fff"/><circle cx="32" cy="32" r="11" stroke="#00a990" stroke-width="3" fill="none"/><path d="M40 40l9 9" stroke="#00a990" stroke-width="4" stroke-linecap="round"/></svg>
  <p class="key-item left" style="top:318px">Halt and fullmane conducts genetic and DNA analysis, then rebalances body chemistry, thus reversing the hair loss process and enabling your own hair to regrow naturally</p>
  <svg class="key-icon" style="left:641px;top:320px" viewBox="0 0 70 70"><circle cx="35" cy="35" r="34" fill="#fff"/><path d="M35 20l12 5v9c0 8-5 13-12 16-7-3-12-8-12-16v-9z" fill="#00a990"/><path d="M29 35l5 5 8-9" stroke="#fff" stroke-width="3" fill="none"/></svg>
  <p class="key-item right" style="top:344px">Money back guaranteed results</p>

  <svg class="key-icon" style="left:482px;top:456px" viewBox="0 0 70 70"><circle cx="35" cy="35" r="34" fill="#fff"/><path d="M34 46c-10 0-13-10-9-20 6 2 11 8 9 20zM36 46c0-10 4-16 11-18 2 10-3 18-11 18z" fill="#00a990"/></svg>
  <p class="key-item left" style="top:470px">Purely Core ingredients – no harsh<br>preservatives or chemicals are included</p>
  <svg class="key-icon" style="left:641px;top:456px" viewBox="0 0 70 70"><circle cx="35" cy="35" r="34" fill="#fff"/><circle cx="35" cy="35" r="14" stroke="#00a990" stroke-width="3" fill="none"/><path d="M28 35l5 5 9-10" stroke="#00a990" stroke-width="3" fill="none"/></svg>
  <p class="key-item right" style="top:470px">All ingredients are FDA approved<br>and safe – no side effects</p>
</section>

<section class="how-it-works">
  <h2 class="section-title" style="top:66px;width:262px">How it works</h2>
  <div class="step-num" style="left:207px;top:203px">1</div>
  <div class="step-num" style="left:469px;top:203px">2</div>
  <div class="step-num" style="left:731px;top:203px">3</div>
  <div class="step-num" style="left:993px;top:203px">4</div>
  <svg class="abs" style="left:300px;top:200px" width="640" height="40" viewBox="0 0 640 40">
    <g stroke="#c9c9cc" stroke-width="1.5" fill="none">
      <path d="M10 30Q80 0 150 22M143 16l7 6-9 3"/>
      <path d="M272 30Q342 0 412 22M405 16l7 6-9 3"/>
      <path d="M534 30Q604 0 674 22"/>
    </g>
  </svg>
  <svg class="abs" style="left:834px;top:200px" width="160" height="40" viewBox="0 0 160 40"><path d="M0 30Q70 0 140 22M133 16l7 6-9 3" stroke="#c9c9cc" stroke-width="1.5" fill="none"/></svg>

  <div class="step" style="left:122px;top:313px"><h3>The science behind the effectiveness of Halt &amp; Fullmane™</h3><p>Halt and Fullmane uses a scientific<br>approach to preventing...</p></div>
  <div class="step" style="left:384px;top:313px"><h3>Personalized Solution Tailored to Your Individual Needs</h3><p>Dr. Pembrook created his solution from<br>a combination of FDA-approved</p></div>
  <div class="step" style="left:646px;top:313px"><h3>What To Expect On the Halt and Fullmane Program</h3><p>Approximately 90% of the men who<br>have started this treatment...</p></div>
  <div class="step" style="left:908px;top:313px"><h3>Worried About Side<br>Effects?</h3><p>You may have read some of<br>the articles online about...</p></div>

  <div class="btn" style="left:500px;top:478px;width:200px;height:40px">See how it works</div>
</section>

<section>
  <h2 class="section-title" style="top:2521px;width:262px">Success stories</h2>
  <svg class="nav-arrow" style="left:376px" viewBox="0 0 44 44"><circle cx="22" cy="22" r="22" fill="#c2c2c2"/><path d="M25 14l-8 8 8 8" stroke="#fff" stroke-width="2.5" fill="none"/></svg>
  <div class="story-photo" style="left:467px" role="img" aria-label="Top of scalp before the program, showing thinning"></div>
  <div class="story-photo" style="left:602px" role="img" aria-label="Top of scalp after 16 months, showing regrowth"></div>
  <svg class="nav-arrow" style="left:764px" viewBox="0 0 44 44"><circle cx="22" cy="22" r="22" fill="#c2c2c2"/><path d="M19 14l8 8-8 8" stroke="#fff" stroke-width="2.5" fill="none"/></svg>
  <p class="story-caption">Leo Before and After 16 Months on the Program</p>
  <p class="story-text">When Leo first came to see us he was experiencing diffuse thinning all over the top third of his scalp. While less common we do see this regularly. Luckily for Leo he came to see us in time and we were able to save all his hair. The picture on the right shows Leo's progress after just 16 Months on the Halt and Fullmane program.</p>
</section>

<footer class="site-footer">
  <div class="footer-brand">
    <div class="brand-mark"></div>
    <div><div class="brand-name">Halt &amp; Fullmane</div><div class="brand-by">by Graham Pembrook M.D.</div></div>
  </div>
  <h4 style="left:583px;top:56px">Contact us</h4>
  <svg class="abs" style="left:580px;top:100px" width="14" height="20" viewBox="0 0 14 20"><path d="M7 0a7 7 0 0 1 7 7c0 5-7 13-7 13S0 12 0 7a7 7 0 0 1 7-7z" fill="#fff"/><circle cx="7" cy="7" r="2.5" fill="#33a6d7"/></svg>
  <p class="footer-line" style="left:616px;top:94px">2210 Harbor Crest Ave, Suite 300<br>Riverton CA 90000</p>
  <svg class="abs" style="left:578px;top:150px" width="18" height="18" viewBox="0 0 24 24"><path fill="#fff" d="M6.6 10.8a15 15 0 0 0 6.6 6.6l2.2-2.2a1 1 0 0 1 1-.25 11.4 11.4 0 0 0 3.6.57 1 1 0 0 1 1 1V20a1 1 0 0 1-1 1A17 17 0 0 1 3 4a1 1 0 0 1 1-1h3.5a1 1 0 0 1 1 1c0 1.25.2 2.45.57 3.57a1 1 0 0 1-.25 1z"/></svg>
  <p class="footer-line" style="left:616px;top:149px">(310) 555-0192</p>
  <h4 style="left:872px;top:56px">Hours of operation</h4>
  <p class="footer-line" style="left:872px;top:94px">Monday - Friday: 9.00am to 5.00pm</p>
  <p class="footer-line" style="left:872px;top:126px">Saturday: 8.00am to 2.00pm</p>
  <div class="footer-divider"></div>
  <p class="copyright">Copyrights © 2017 All Rights Reserved</p>
</footer>

</body>
</html>
```